Business card design for my company.
I would like the card's background colour to be black. You can also see our web site to get an idea of our brand. https://www.tmwhomecrafting.com.au/
- Name
- Email

```html
<!DOCTYPE html>
<html lang="en">
<head>
<meta charset="utf-8">
<title>TMW Home Crafting – Business Card</title>
<link href="https://fonts.googleapis.com/css2?family=Open+Sans:wght@400;600;700&display=swap" rel="stylesheet">
<style>
  :root {
    --stage: #2b2c2e;
    --card: #1c1c1d;
    --green: #0f9a3c;
    --white: #f4f4f4;
    --muted: #d9d9d9;
    --rule: #bdbdbd;
  }
  * { box-sizing: border-box; margin: 0; padding: 0; }
  html, body { width: 1200px; height: 1088px; overflow: hidden; }
  body {
    background: var(--stage);
    font-family: "Open Sans", Arial, sans-serif;
    display: flex; flex-direction: column; align-items: center;
    padding-top: 35px; gap: 36px;
  }
  .card {
    position: relative; width: 860px; height: 491px;
    background: var(--card); overflow: hidden;
    box-shadow: 0 8px 24px rgba(0,0,0,.45);
  }
  .brand {
    position: absolute; display: flex; align-items: center; gap: 14px;
    color: var(--white); font-weight: 700; letter-spacing: 3px;
    text-transform: uppercase; white-space: nowrap;
  }
  .brand-square { width: 22px; height: 22px; background: var(--green); flex: none; }
  .card-front .brand { right: 56px; top: 130px; font-size: 34px; }
  .card-back .brand { left: 50%; top: 50%; transform: translate(-50%, -50%); font-size: 52px; gap: 20px; }
  .card-back .brand-square { width: 32px; height: 32px; }

  .divider { position: absolute; left: 60px; right: 40px; top: 318px; height: 1px; background: var(--rule); }
  .person { position: absolute; left: 60px; top: 246px; }
  .person-name { color: var(--green); font-weight: 700; font-size: 26px; letter-spacing: .5px; text-transform: uppercase; line-height: 1.1; }
  .person-role { color: var(--white); font-size: 21px; line-height: 1.3; }
  .contact { position: absolute; left: 60px; top: 338px; list-style: none; }
  .contact li { display: flex; align-items: center; gap: 10px; color: var(--white); font-size: 21px; line-height: 1.5; }
  .contact svg { width: 16px; height: 16px; fill: var(--green); flex: none; }
  .address { position: absolute; right: 44px; top: 338px; text-align: right; color: var(--white); font-size: 20px; line-height: 1.3; }
  .footer-band { position: absolute; left: 0; bottom: 0; width: 860px; height: 110px; }
  .website { position: absolute; right: 44px; bottom: 36px; color: var(--white); font-size: 20px; }
</style>
</head>
<body>
  <section class="card card-front" aria-label="Card front">
    <div class="brand"><span class="brand-square"></span>TMW Home Crafting</div>
    <div class="person">
      <p class="person-name">Daniel Hartley</p>
      <p class="person-role">Managing Director</p>
    </div>
    <div class="divider"></div>
    <ul class="contact">
      <li><svg viewBox="0 0 16 16" aria-hidden="true"><path d="M3 1l3 0 1 4-2 1.5c.8 1.8 2.2 3.2 4 4L10.5 8.5l4 1v3c0 1-1 2-2 2C6.5 14.5 1.5 9.5 1.5 3c0-1 .5-2 1.5-2z"/></svg>0400 123 456</li>
      <li><svg viewBox="0 0 16 16" aria-hidden="true"><path d="M1 3h14v10H1z M2 4l6 5 6-5" /></svg>info@tmwhomecrafting.com.au</li>
    </ul>
    <p class="address">Launceston, Tasmania<br>Australia</p>
    <svg class="footer-band" viewBox="0 0 860 110" aria-hidden="true">
      <path d="M0 110 L0 88 L400 88 L430 58 L430 58 L860 58 L860 110 Z" fill="var(--green)"/>
      <path d="M0 74 L392 74 L430 38 L860 38 L860 58 L430 58 L400 88 L0 88 Z" fill="var(--card)"/>
      <path d="M0 78 L394 78 L432 42 L432 50 L398 84 L0 84 Z" fill="var(--white)"/>
    </svg>
    <p class="website">www.tmwhomecrafting.com.au</p>
  </section>

  <section class="card card-back" aria-label="Card back">
    <div class="brand"><span class="brand-square"></span>TMW Home Crafting</div>
  </section>
</body>
</html>
```